I need a business card designed using the logo provided either vertical or horizontal......Harbourline Property Group is an Australian based real estate company that caters for the upper end of the market so the design of the business card "must reflect" the companies image!!
Colour combinations are optional but "must be realistic" and must be able to be accurately useable CMYK colours.
Please consider that any colours used "must be able to be used" and be suitable in following designs for "pull out banner signs" and "real estate signs".
The colours and the font in the attached designs are for example and other combinations are encouraged.
Target Market(s)
The High End of the Australian real estate market
Industry/Entity Type
Business
Contact Information for Business Card
Logo - Business Name - Director + Licensed Real Estate Agent - Mobile Number (Cell Phone) - Business Number - Fax - Email Address - Web address
Requirements
Must have
- Designs and colours (CMYK) that can easily be interpreted by an Australian printer.
Nice to have
- Some alternative ideas on colour and font..........the ones provided are ok and have been provided as an example but I am looking for alternative ideas
Should not have
- Loud, overly bright colours. Designs that do not reflect the professional standards of the business.
- Designs that look good on a computer monitor but can not be re-created on a printing press.............this is most important when it comes to shading etc.

```html
<!DOCTYPE html>
<html lang="en">
<head>
<meta charset="utf-8">
<title>Harbourline Property Group – Business Card</title>
<link rel="stylesheet" href="https://fonts.googleapis.com/css2?family=Open+Sans:wght@400;600;700&display=swap">
<style>
  :root {
    --canvas: #ecebe8;
    --card-white: #ffffff;
    --gold-light: #dcbd45;
    --gold-deep: #b8952c;
    --ink: #2b2622;
    --divider: #2b2622;
    --text-on-gold: #ffffff;
    --shadow: rgba(0, 0, 0, 0.14);
  }
  * { margin: 0; padding: 0; box-sizing: border-box; }
  html, body {
    width: 1200px; height: 818px; overflow: hidden;
    background: var(--canvas);
    font-family: "Open Sans", Arial, sans-serif;
  }
  .stage {
    position: relative; width: 1200px; height: 818px;
    display: flex; align-items: center; justify-content: center; gap: 60px;
  }
  .card {
    position: relative; width: 520px; height: 298px;
    border-radius: 18px; overflow: hidden;
    background: var(--card-white);
    box-shadow: 0 10px 30px var(--shadow);
  }
  .card-front .gold-field { position: absolute; inset: 0; }
  .brand {
    position: absolute; display: flex; align-items: center; gap: 12px;
    color: var(--ink); font-weight: 600; letter-spacing: 0.06em;
    text-transform: uppercase;
  }
  .brand-mark { background: var(--gold-deep); flex: none; }
  .card-front .brand { top: 40px; right: 34px; font-size: 17px; line-height: 1.25; }
  .card-front .brand-mark { width: 30px; height: 30px; }
  .person {
    position: absolute; left: 34px; top: 150px; color: var(--text-on-gold);
  }
  .person-name { font-size: 22px; font-weight: 700; line-height: 1.1; }
  .person-role { font-size: 13px; color: var(--ink); margin-top: 2px; }
  .contact {
    position: absolute; left: 34px; top: 204px; list-style: none;
    color: var(--text-on-gold); font-size: 12px; line-height: 1.3;
  }
  .contact-address { margin-bottom: 5px; }
  .contact-line { display: flex; align-items: center; gap: 8px; }
  .contact-icon { width: 13px; height: 13px; flex: none; }
  .card-back .brand {
    left: 50%; top: 50%; transform: translate(-50%, -50%);
    font-size: 22px; white-space: nowrap;
  }
  .card-back .brand-mark { width: 38px; height: 38px; }
  .card-back .edge-band {
    position: absolute; left: 0; right: 0; bottom: 0; height: 14px;
    background: linear-gradient(90deg, var(--gold-deep), var(--gold-light));
  }
</style>
</head>
<body>
<main class="stage">
  <section class="card card-front">
    <svg class="gold-field" viewBox="0 0 520 298" width="520" height="298">
      <defs>
        <linearGradient id="goldFill" x1="0" y1="1" x2="1" y2="0">
          <stop offset="0" stop-color="#b8952c"/>
          <stop offset="1" stop-color="#dcbd45"/>
        </linearGradient>
      </defs>
      <path d="M0 128 Q300 108 520 196 L520 298 L0 298 Z" fill="url(#goldFill)"/>
      <path d="M0 124 Q300 104 520 192" fill="none" stroke="#2b2622" stroke-width="3"/>
    </svg>
    <div class="brand">
      <span class="brand-mark"></span>
      <span>Harbourline<br>Property Group</span>
    </div>
    <div class="person">
      <p class="person-name">Employee Name</p>
      <p class="person-role">Managing Director</p>
    </div>
    <ul class="contact">
      <li class="contact-address">12 Bay Street<br>Double Bay, NSW 2028</li>
      <li class="contact-line">
        <svg class="contact-icon" viewBox="0 0 16 16"><circle cx="8" cy="8" r="8" fill="#2b2622"/><path d="M5 4.5h2l.6 2-1 .8a5 5 0 0 0 2.1 2.1l.8-1 2 .6v2a1 1 0 0 1-1 1A6.5 6.5 0 0 1 4 5.5a1 1 0 0 1 1-1z" fill="#fff"/></svg>
        <span>0412 345 678</span>
      </li>
      <li class="contact-line">
        <svg class="contact-icon" viewBox="0 0 16 16"><circle cx="8" cy="8" r="8" fill="#2b2622"/><rect x="4" y="5" width="8" height="6" fill="#fff"/><path d="M4 5l4 3.2L12 5" fill="none" stroke="#2b2622" stroke-width="1"/></svg>
        <span>info@harbourlinegroup.com.au</span>
      </li>
      <li class="contact-line">
        <svg class="contact-icon" viewBox="0 0 16 16"><circle cx="8" cy="8" r="8" fill="#2b2622"/><circle cx="8" cy="8" r="4.5" fill="none" stroke="#fff"/><path d="M3.5 8h9M8 3.5c-2 2.5-2 6.5 0 9M8 3.5c2 2.5 2 6.5 0 9" fill="none" stroke="#fff" stroke-width="0.8"/></svg>
        <span>www.harbourlinegroup.com.au</span>
      </li>
    </ul>
  </section>

  <section class="card card-back">
    <div class="brand">
      <span class="brand-mark"></span>
      <span>Harbourline Property Group</span>
    </div>
    <div class="edge-band"></div>
  </section>
</main>
</body>
</html>
```